KBT Business Cards

We require business cards for our business. We would like a matte black back to the card, with our logo centred in the middle. The front side of the card is open to design.

Target Market(s)

Clients looking for legal services (professional)

Industry/Entity Type

Legal

Contact Information for Business Card

Doran Kelbrath
Partner
Mobile: 0461 738 524
Email: doran@kbtlaw.co
Website: www.kbtlaw.co
Level 3, 118 Wendmore Street
Sydney NSW 2000

Font styles to use
Other font styles liked:
• Avenir

Colors
f04a50
ffffff
1b1b1b

Requirements
Must have
• Black back with logo included in the centre of the card.
• Our font is Avenir.

```html
<!DOCTYPE html>
<html lang="en">
<head>
<meta charset="utf-8">
<title>KBT Business Cards</title>
<link rel="stylesheet" href="https://fonts.googleapis.com/css2?family=Roboto:wght@400;700&display=swap">
<style>
  :root {
    --backdrop: #2b2b2d;
    --card: #1b1b1b;
    --card-edge: #111111;
    --accent: #d41c48;
    --white: #ffffff;
    --muted: #c9c9c9;
    --rule: #8a8a8a;
  }
  * { margin: 0; padding: 0; box-sizing: border-box; }
  html, body { width: 1200px; height: 900px; overflow: hidden; }
  body {
    background: var(--backdrop);
    font-family: "Roboto", sans-serif;
    position: relative;
  }
  .card {
    position: absolute;
    left: 340px;
    width: 520px;
    height: 300px;
    background: linear-gradient(160deg, #222 0%, var(--card) 55%, var(--card-edge) 100%);
    border-bottom: 9px solid var(--accent);
    box-shadow: 0 10px 24px rgba(0,0,0,.45);
    overflow: hidden;
  }
  .card--front { top: 110px; }
  .card--back { top: 480px; }

  /* front: brand lockup */
  .brand {
    position: absolute;
    left: 0; right: 0; top: 0; bottom: 0;
    display: flex;
    align-items: center;
    justify-content: center;
    gap: 22px;
  }
  .brand__mark {
    width: 58px;
    height: 58px;
    background: var(--accent);
  }
  .brand__name {
    color: var(--white);
    font-weight: 700;
    font-size: 27px;
    line-height: 1.02;
    letter-spacing: .5px;
    text-transform: uppercase;
  }

  /* back: contact details */
  .person {
    position: absolute;
    right: 290px;
    top: 118px;
    text-align: right;
  }
  .person__name {
    color: var(--accent);
    font-weight: 700;
    font-size: 17px;
    letter-spacing: .3px;
    text-transform: uppercase;
  }
  .person__role {
    color: var(--muted);
    font-size: 13px;
    margin-top: 3px;
  }
  .divider {
    position: absolute;
    left: 250px;
    top: 112px;
    width: 1px;
    height: 70px;
    background: var(--rule);
  }
  .contacts {
    position: absolute;
    left: 270px;
    top: 122px;
    list-style: none;
  }
  .contacts li {
    display: flex;
    align-items: center;
    gap: 7px;
    color: var(--white);
    font-size: 14px;
    line-height: 19px;
  }
  .contacts svg { width: 11px; height: 11px; fill: var(--accent); flex: none; }
  .address {
    position: absolute;
    left: 60px;
    bottom: 36px;
    color: var(--muted);
    font-size: 14.5px;
    letter-spacing: .2px;
  }
</style>
</head>
<body>

<section class="card card--front" aria-label="Card back with brand">
  <div class="brand">
    <div class="brand__mark"></div>
    <div class="brand__name">Kelbrath<br>Bannick<br>Legal</div>
  </div>
</section>

<section class="card card--back" aria-label="Card front with contact details">
  <div class="person">
    <p class="person__name">Doran Kelbrath</p>
    <p class="person__role">Partner</p>
  </div>
  <div class="divider"></div>
  <ul class="contacts">
    <li>
      <svg viewBox="0 0 12 12" aria-hidden="true"><path d="M2.5 1h2l1 3-1.5 1a7 7 0 0 0 3 3l1-1.5 3 1v2a1.5 1.5 0 0 1-1.5 1.5A9.5 9.5 0 0 1 1 2.5 1.5 1.5 0 0 1 2.5 1z"/></svg>
      0461 738 524
    </li>
    <li>
      <svg viewBox="0 0 12 12" aria-hidden="true"><path d="M1 2.5h10v7H1z M1 2.5l5 4 5-4" stroke="#1b1b1b" stroke-width=".9"/></svg>
      doran@kbtlaw.co
    </li>
    <li>
      <svg viewBox="0 0 12 12" aria-hidden="true"><circle cx="6" cy="6" r="5"/><path d="M1 6h10M6 1c-2.5 3-2.5 7 0 10M6 1c2.5 3 2.5 7 0 10" stroke="#1b1b1b" stroke-width=".8" fill="none"/></svg>
      www.kbtlaw.co
    </li>
  </ul>
  <p class="address">Level 3, 118 Wendmore Street Sydney NSW 2000</p>
</section>

</body>
</html>
```